Quillmarsh Property Solutions need a business card design

Hello guys. We would need a business card design asap please.
We are a start up property investment business based in London UK specialised in buying, selling, managing and letting properties and helping distressed property owners.
The name of our Business is Quillmarsh, the logo symbolises the four fundamental elements of the world (earth, air, fire and water) and so it stands for strength, stability, longevity.
We would like the business card to communicate professionalism and reliability. Many many thanks indeed for your work.

Details:

1.) Rosalind Updike
Property Investor
Mobile: +44(0)7700123456
Email: rosalind.quillmarsh@mailbox-example.com

2.) Dominic Updike
Property Investor
Mobile: +44(0)7700987654
Email: dominic.quillmarsh@mailbox-example.com

```html
<!DOCTYPE html>
<html lang="en">
<head>
<meta charset="utf-8">
<title>Quillmarsh Property Solutions – Business Card</title>
<link rel="stylesheet" href="https://fonts.googleapis.com/css2?family=Jost:wght@700&family=Lato:wght@400;700&display=swap">
<style>
  :root {
    --stage: #e6e7e9;
    --card: #fbfbfb;
    --brand-grey: #8a8a8a;
    --ink: #141414;
    --name-blue: #2f5fb3;
    --role-green: #2e9a3c;
    --label-red: #d3222b;
    --deco-red: #e0303a;
    --deco-blue: #2c62c0;
    --deco-green: #2c9a44;
  }
  * { box-sizing: border-box; margin: 0; padding: 0; }
  html, body { width: 1200px; height: 926px; overflow: hidden; }
  body {
    background: var(--stage);
    display: flex;
    flex-direction: column;
    align-items: center;
    justify-content: center;
    gap: 40px;
    font-family: "Lato", Arial, sans-serif;
  }
  .card {
    width: 720px;
    height: 412px;
    background: var(--card);
    box-shadow: 0 6px 18px rgba(0,0,0,0.18);
    position: relative;
    overflow: hidden;
  }
  .brand-name {
    font-family: "Jost", Arial, sans-serif;
    font-weight: 700;
    text-transform: uppercase;
    line-height: 1.05;
  }

  /* Front */
  .card--front {
    display: flex;
    flex-direction: column;
    align-items: center;
    justify-content: center;
    gap: 22px;
  }
  .card--front .brand-mark {
    width: 26px;
    height: 26px;
    background: var(--brand-grey);
  }
  .card--front .brand-name {
    color: var(--brand-grey);
    text-align: center;
    font-size: 44px;
    letter-spacing: 3px;
  }
  .card--front .brand-name small {
    display: block;
    font-size: 22px;
    letter-spacing: 2px;
    margin-top: 6px;
  }

  /* Back */
  .card--back .decor {
    position: absolute;
    left: 0; top: 0;
    width: 250px;
    height: 100%;
  }
  .card--back .details {
    position: absolute;
    left: 290px;
    top: 40px;
    right: 24px;
  }
  .card--back .brand-name {
    color: var(--ink);
    font-size: 36px;
    letter-spacing: 2px;
  }
  .card--back .brand-name small {
    display: block;
    font-size: 16px;
    letter-spacing: 1px;
    margin-top: 4px;
  }
  .contact { margin-top: 30px; }
  .contact + .contact { margin-top: 20px; }
  .contact__name { color: var(--name-blue); font-size: 24px; line-height: 1.1; }
  .contact__role { color: var(--role-green); font-size: 15px; letter-spacing: 1px; margin-bottom: 4px; }
  .contact__line { color: var(--ink); font-size: 16px; line-height: 1.45; }
  .contact__label { color: var(--label-red); font-weight: 700; }
</style>
</head>
<body>
  <section class="card card--front">
    <span class="brand-mark"></span>
    <h1 class="brand-name">Quillmarsh<small>Property Solutions</small></h1>
  </section>

  <section class="card card--back">
    <svg class="decor" viewBox="0 0 250 412" preserveAspectRatio="none" role="img" aria-label="Decorative brand artwork in red, blue and green tones">
      <defs>
        <linearGradient id="decorFill" x1="0" y1="0" x2="0" y2="1">
          <stop offset="0" stop-color="var(--deco-red)"/>
          <stop offset="0.45" stop-color="#c9d6ef"/>
          <stop offset="0.8" stop-color="var(--deco-blue)"/>
          <stop offset="1" stop-color="var(--deco-green)"/>
        </linearGradient>
      </defs>
      <rect width="250" height="412" fill="url(#decorFill)"/>
    </svg>
    <div class="details">
      <h2 class="brand-name">Quillmarsh<small>Property Solutions</small></h2>
      <div class="contact">
        <p class="contact__name">Dominic Updike</p>
        <p class="contact__role">Property Investor</p>
        <p class="contact__line"><span class="contact__label">m:</span> +44(0)7700987654</p>
        <p class="contact__line"><span class="contact__label">e:</span> dominic.quillmarsh@mailbox-example.com</p>
      </div>
      <div class="contact">
        <p class="contact__name">Rosalind Updike</p>
        <p class="contact__role">Property Investor</p>
        <p class="contact__line"><span class="contact__label">m:</span> +44(0)7700123456</p>
        <p class="contact__line"><span class="contact__label">e:</span> rosalind.quillmarsh@mailbox-example.com</p>
      </div>
    </div>
  </section>
</body>
</html>
```